Brightway Haul & Upkeep Services, are a company that offers a 'one stop shop' pre-move clean up a

I have already selected a logo which I would like on the front of the business cards along with phone numbers, web address and email which are:
0487650392
www.brightwayhaul.com.au
brightwayhaulandupkeep@mailbox.example

On the back of the card I would like to list some of the types of service we offer (clean - move - repairs/maintenance) which are:
CLEAN - windows, gutters, solar panels, driveways/paths, carpets.
MOVE - Small/medium size house/office moves, large item pick-up & delivery, yard clean-up and removal.
General maintenance and repairs.

I would like the blue logo on a gray background.

Thanks

```html
<!DOCTYPE html>
<html lang="en">
<head>
<meta charset="utf-8">
<title>Brightway Haul &amp; Upkeep Services – Business Cards</title>
<link rel="stylesheet" href="https://fonts.googleapis.com/css2?family=Open+Sans:wght@400;600;700&display=swap">
<style>
  :root {
    --brand-blue: #1f6db5;
    --sky-blue: #7dbbe8;
    --ink: #1f1f1f;
    --paper: #ffffff;
    --backdrop: #e4e5e7;
    --edge: #3a3a3a;
  }
  * { box-sizing: border-box; margin: 0; padding: 0; }
  html, body {
    width: 1200px; height: 1073px; overflow: hidden;
    background: var(--backdrop);
    font-family: "Open Sans", Arial, sans-serif;
  }
  .canvas { position: relative; width: 1200px; height: 1073px; }
  .card {
    position: absolute; width: 836px; height: 476px;
    background: var(--paper); border: 1px solid var(--edge);
    border-radius: 40px; overflow: hidden;
  }
  .card--front { left: 42px; top: 42px; }
  .card--back { left: 324px; top: 553px; }
  .wave { position: absolute; left: 0; top: 0; width: 836px; height: 476px; }
  .phone {
    position: absolute; left: 566px; top: 56px;
    color: var(--paper); font-size: 29px; font-weight: 400;
    display: flex; align-items: center; gap: 8px;
  }
  .phone svg { width: 24px; height: 24px; }
  .brand-name {
    color: var(--brand-blue); font-weight: 700; line-height: 1.05;
  }
  .card--front .brand-name { position: absolute; left: 52px; top: 190px; }
  .brand-name .line-main { display: block; font-size: 60px; letter-spacing: -1px; }
  .brand-name .line-sub { display: block; font-size: 31px; margin-top: 6px; }
  .contact {
    position: absolute; left: 55px; top: 376px;
    list-style: none; color: var(--ink); font-size: 22px;
  }
  .contact li { display: flex; align-items: center; gap: 9px; height: 33px; }
  .contact .web { letter-spacing: 1.6px; }
  .contact svg { width: 19px; height: 19px; flex: none; }
  .card--back .brand-name {
    position: absolute; left: 0; right: 0; top: 130px; text-align: center;
  }
  .services-title {
    position: absolute; left: 0; right: 0; top: 283px; text-align: center;
    color: var(--brand-blue); font-size: 34px; font-weight: 700; letter-spacing: 3px;
  }
  .service-list {
    position: absolute; left: 0; right: 0; top: 354px;
    text-align: center; color: var(--ink); font-size: 26px; font-weight: 600;
  }
  .service-list p { height: 43px; }
  .service-list .item { margin: 0 12px; }
  .service-list .item::before { content: "• "; color: var(--brand-blue); }
</style>
</head>
<body>
<main class="canvas">
  <section class="card card--front" aria-label="Card front">
    <svg class="wave" viewBox="0 0 836 476" aria-hidden="true">
      <path d="M0,0 H836 V243 C600,140 320,10 0,70 Z" fill="var(--brand-blue)"/>
      <path d="M0,70 C320,10 600,140 836,243 V285 C600,170 320,35 0,84 Z" fill="var(--sky-blue)"/>
      <path d="M0,78 C320,22 600,150 836,262 V270 C600,160 320,32 0,84 Z" fill="var(--paper)"/>
    </svg>
    <div class="phone">
      <svg viewBox="0 0 24 24" aria-hidden="true"><circle cx="12" cy="12" r="10.5" fill="none" stroke="#fff" stroke-width="1.6"/><path d="M8.5 6.5c-1 .8-1.2 2.2-.5 3.8 1 2.3 2.8 4.3 5 5.5 1.5.8 2.9.6 3.7-.4l-2-1.8-1.3.8c-1.3-.7-2.6-2-3.3-3.4l.8-1.2z" fill="#fff"/></svg>
      <span>0487650392</span>
    </div>
    <h1 class="brand-name"><span class="line-main">BRIGHTWAY HAUL</span><span class="line-sub">&amp; UPKEEP SERVICES</span></h1>
    <ul class="contact">
      <li>
        <svg viewBox="0 0 20 20" aria-hidden="true"><rect x="1" y="5" width="18" height="12" rx="1.5" fill="var(--brand-blue)"/><path d="M1.5 6 10 12l8.5-6" fill="none" stroke="#fff" stroke-width="1.4"/></svg>
        <span>brightwayhaulandupkeep@mailbox.example</span>
      </li>
      <li class="web">
        <svg viewBox="0 0 20 20" aria-hidden="true"><circle cx="10" cy="10" r="8.5" fill="none" stroke="var(--brand-blue)" stroke-width="1.5"/><ellipse cx="10" cy="10" rx="3.5" ry="8.5" fill="none" stroke="var(--brand-blue)" stroke-width="1.2"/><path d="M1.5 10h17M3 6h14M3 14h14" stroke="var(--brand-blue)" stroke-width="1.2"/></svg>
        <span>www.brightwayhaul.com.au</span>
      </li>
    </ul>
  </section>

  <section class="card card--back" aria-label="Card back">
    <h2 class="brand-name"><span class="line-main">BRIGHTWAY HAUL</span><span class="line-sub">&amp; UPKEEP SERVICES</span></h2>
    <h3 class="services-title">Services we offer</h3>
    <div class="service-list">
      <p><span class="item">Clean</span><span class="item">Move</span></p>
      <p><span class="item">General Maintenance And Repairs.</span></p>
    </div>
  </section>
</main>
</body>
</html>
```